13 Varno - new website design project

Our company Varno Electrical is developing a new lead generation website focused on Electrical, LED Lighting and Solar Power. We need a high converting website.

Example of our current website is www.varnoelectrical-example.com.au You can take content from this website for this new design. Our colours are red, black and white. For our new website we would like to promote Varno, Spark Every Day. Please listen to the jingle.

The below link is the company jingle that we have developed.
http://www.tunecraftdemo.com.au/vrn-tc-v1/

The key for this brief is to generate leads for Electrical, LED Lighting (for commercial) and Solar Power & Storage.

Target Market(s)

Business owners in Melbourne Victoria

Number of Pages Required

4 page

Colors
ec1f27
ffffff

Requirements
Must have
• This page must be clean, be in line with company branding and a high converting lead website.

```html
<!DOCTYPE html>
<html lang="en">
<head>
<meta charset="utf-8">
<title>Varno Electrical</title>
<link rel="stylesheet" href="https://fonts.googleapis.com/css2?family=Open+Sans:wght@400;600;700;800&display=swap">
<style>
:root{
  --red:#ec1f27;
  --dark:#1d1d1d;
  --text:#555;
  --grey-bg:#f6f6f6;
  --footer-bg:#f4f4f4;
  --bar-bg:#e9e9e9;
  --diamond:#3c3c3c;
  --white:#fff;
}
*{box-sizing:border-box;margin:0;padding:0}
html,body{width:1200px;height:2727px;overflow:hidden}
body{font-family:'Open Sans',Arial,sans-serif;color:var(--text);background:var(--white);position:relative}
a{color:inherit;text-decoration:none}
.header{position:absolute;top:0;left:0;width:1200px;height:120px}
.brand{position:absolute;left:100px;top:24px;display:flex;align-items:center;gap:12px}
.brand-dot{width:46px;height:46px;border-radius:50%;background:var(--red)}
.brand-name{font-size:40px;font-weight:800;color:var(--dark);letter-spacing:1px}
.call{position:absolute;right:98px;top:18px;display:flex;align-items:center;gap:12px}
.call-icon{width:40px;height:40px;border-radius:50%;background:var(--red);display:flex;align-items:center;justify-content:center}
.call-label{color:var(--red);font-weight:700;font-size:17px}
.call-number{color:var(--dark);font-weight:700;font-size:26px;margin-left:2px}
.nav{position:absolute;right:98px;top:76px;display:flex;gap:46px;font-size:14.5px;font-weight:600;color:var(--dark)}
.nav .active{color:var(--red)}
.hero{position:absolute;top:120px;left:0;width:1200px;height:452px;background:linear-gradient(180deg,#2d7fd6 0%,#6fb3ee 45%,#bcdcf2 72%,#d8c268 88%,#b89a2c 100%)}
.hero-title{position:absolute;left:142px;top:110px;font-size:64px;font-weight:800;color:var(--white);letter-spacing:1px}
.hero-text{position:absolute;left:142px;top:200px;width:440px;font-size:15px;line-height:27px;color:var(--white);font-weight:600}
.btn-ghost{position:absolute;left:142px;top:283px;width:180px;height:42px;border:2px solid var(--white);border-radius:22px;color:var(--white);font-size:14px;font-weight:700;display:flex;align-items:center;justify-content:center}
.hero-arrow{position:absolute;top:200px}
.welcome{position:absolute;top:572px;left:0;width:1200px;height:492px;text-align:center}
.section-title{font-size:25px;font-weight:700;color:var(--dark)}
.welcome .section-title{margin-top:52px}
.welcome-sub{font-size:14.5px;margin-top:8px}
.services{position:absolute;top:150px;left:0;width:1200px}
.service{position:absolute;width:300px;text-align:center}
.service-ring{width:124px;height:124px;margin:0 auto;border:2px solid var(--red);border-radius:50%;display:flex;align-items:center;justify-content:center}
.service-icon{width:106px;height:106px;border-radius:50%;background:var(--red);display:flex;align-items:center;justify-content:center}
.service h3{font-size:17px;font-weight:600;color:var(--dark);margin-top:24px}
.service p{font-size:12.5px;line-height:25px;margin-top:10px}
.btn-line{display:inline-flex;align-items:center;justify-content:center;width:110px;height:34px;border:1.5px solid var(--red);border-radius:18px;color:var(--red);font-size:12.5px;margin-top:20px}
.about{position:absolute;top:1064px;left:0;width:600px;height:423px;background:var(--grey-bg)}
.about .section-title{position:absolute;left:98px;top:68px}
.about-text{position:absolute;left:98px;top:116px;width:440px;font-size:12.5px;line-height:26px}
.about-text p+p{margin-top:10px}
.about .btn-line{position:absolute;left:98px;top:306px;margin:0}
.photo{position:absolute}
.photo-building{top:1064px;left:600px;width:600px;height:423px;background:linear-gradient(180deg,#d6d0ec 0%,#e9e3ee 38%,#aab4bc 52%,#c4262e 66%,#3a3a3a 88%,#555 100%)}
.photo-tools{top:1487px;left:0;width:600px;height:424px;background:linear-gradient(135deg,#f1f1f1 0%,#e4e4e4 40%,#c9d0de 60%,#d7d7d7 100%)}
.why{position:absolute;top:1487px;left:600px;width:600px;height:424px;background:var(--grey-bg)}
.why .section-title{position:absolute;left:67px;top:40px}
.why-list{position:absolute;left:67px;top:96px;width:470px;list-style:none}
.why-item{display:flex;align-items:flex-start;margin-bottom:20px}
.diamond{width:26px;height:26px;margin:6px 20px 0 6px;transform:rotate(45deg);background:var(--diamond);flex:none;display:flex;align-items:center;justify-content:center}
.diamond span{transform:rotate(-45deg);color:var(--white);font-size:13px;font-weight:700}
.why-item.first .diamond{background:var(--red)}
.why-body{border-left:1.5px solid #bbb;padding-left:22px;min-height:36px}
.why-body h4{font-size:17px;font-weight:400;color:var(--dark);line-height:36px}
.why-body p{font-size:12px;line-height:22px;margin-top:-4px}
.reviews{position:absolute;top:1911px;left:0;width:1200px;height:300px}
.reviews .section-title{text-align:center;margin-top:47px}
.review{position:absolute;top:110px;width:500px;height:140px}
.review-photo{position:absolute;left:0;top:0;width:130px;height:130px;border-radius:50%;background:radial-gradient(circle at 50% 40%,#d9d9d9,#7d7d7d);border:4px solid #eee}
.review-text{position:absolute;left:152px;top:8px;width:348px;font-size:12.5px;line-height:24px;text-align:justify}
.review-name{position:absolute;right:0;top:96px;font-size:15px;font-weight:700;color:var(--dark)}
.review-name em{font-style:normal;color:var(--red)}
.divider{position:absolute;top:2209px;left:97px;width:1003px;height:1px;background:#bbb}
.clients{position:absolute;top:2250px;left:97px;width:1003px;display:flex;justify-content:space-between}
.client{width:222px;height:100px;border:1px solid #ddd;display:flex;align-items:center;justify-content:center;font-size:21px;font-weight:700;color:var(--dark)}
.footer{position:absolute;top:2405px;left:0;width:1200px;height:270px;background:var(--footer-bg)}
.col{position:absolute;top:60px}
.col h5{font-size:17px;font-weight:700;color:var(--dark);margin-bottom:16px}
.col ul{list-style:none;font-size:12.5px;line-height:24px}
.col li::before{content:"»";margin-right:16px;color:var(--dark)}
.col.hours li::before{content:none}
.field{width:250px;height:33px;border:1px solid #bbb;background:var(--white);font-size:12px;color:#999;padding:0 12px;display:flex;align-items:center;margin-bottom:8px}
.submit{width:250px;height:33px;background:var(--red);color:var(--white);font-size:15px;display:flex;align-items:center;justify-content:center}
.bottom-bar{position:absolute;top:2675px;left:0;width:1200px;height:52px;background:var(--bar-bg);font-size:12px;color:#888;text-align:center;line-height:52px}
</style>
</head>
<body>
<header class="header">
  <a class="brand" href="#"><span class="brand-dot"></span><span class="brand-name">Varno</span></a>
  <div class="call">
    <span class="call-icon"><svg width="18" height="18" viewBox="0 0 24 24"><path fill="#fff" d="M6.6 10.8a15 15 0 0 0 6.6 6.6l2.2-2.2c.3-.3.7-.4 1-.2 1.1.4 2.3.6 3.6.6.6 0 1 .4 1 1V20c0 .6-.4 1-1 1A17 17 0 0 1 3 4c0-.6.4-1 1-1h3.5c.6 0 1 .4 1 1 0 1.3.2 2.5.6 3.6.1.3 0 .7-.2 1z"/></svg></span>
    <span class="call-label">CALL US ON</span><span class="call-number">130 555</span>
  </div>
  <nav class="nav">
    <a class="active" href="#">Home</a><a href="#">Varno Story</a><a href="#">Electrical</a><a href="#">Led Lighting</a><a href="#">Solar Power</a><a href="#">Our Work</a><a href="#">Contact Us</a>
  </nav>
</header>

<section class="hero" role="img" aria-label="Wind turbines and solar panels under a blue sky">
  <svg class="hero-arrow" style="left:46px" width="24" height="60" viewBox="0 0 24 60"><path d="M20 2 4 30l16 28" fill="none" stroke="#fff" stroke-width="2"/></svg>
  <svg class="hero-arrow" style="right:46px" width="24" height="60" viewBox="0 0 24 60"><path d="M4 2l16 28L4 58" fill="none" stroke="#fff" stroke-width="2"/></svg>
  <h1 class="hero-title">WE ARE VARNO</h1>
  <p class="hero-text">Our company Varno Electrical is developing a new lead generation website focused on Electrical, LED Lighting and Solar Power.</p>
  <a class="btn-ghost" href="#">GET MORE INFO &gt;&gt;</a>
</section>

<section class="welcome">
  <h2 class="section-title">WELCOME TO VARNO</h2>
  <p class="welcome-sub">Australia's largest fully integrated electrical &amp; energy solutions provider</p>
  <div class="services">
    <div class="service" style="left:116px">
      <div class="service-ring"><div class="service-icon"><svg width="50" height="50" viewBox="0 0 50 50"><g fill="none" stroke="#fff" stroke-width="3.5" stroke-linecap="round"><path d="M18 6v10M32 6v10"/><path d="M12 16h26v8a13 13 0 0 1-26 0z" fill="#fff"/><path d="M25 37v8"/></g><path d="M27 20l-6 8h4l-2 6 6-8h-4z" fill="#ec1f27"/></svg></div></div>
      <h3>ELECTRICAL</h3>
      <p>Great value money, great service reliability.<br>These are the key foundations</p>
      <a class="btn-line" href="#">READ MORE</a>
    </div>
    <div class="service" style="left:450px">
      <div class="service-ring"><div class="service-icon"><svg width="50" height="50" viewBox="0 0 50 50"><path d="M25 4a14 14 0 0 0-8 25v6h16v-6A14 14 0 0 0 25 4z" fill="#fff"/><rect x="18" y="37" width="14" height="3" fill="#fff"/><rect x="20" y="42" width="10" height="3" fill="#fff"/><path d="M25 30V14M25 20l-5-5M25 24l5-5" stroke="#ec1f27" stroke-width="2" fill="none"/></svg></div></div>
      <h3>LED LIGHTING</h3>
      <p>Great value money, great service reliability.<br>These are the key foundations</p>
      <a class="btn-line" href="#">READ MORE</a>
    </div>
    <div class="service" style="left:784px">
      <div class="service-ring"><div class="service-icon"><svg width="54" height="54" viewBox="0 0 54 54"><circle cx="27" cy="27" r="20" fill="none" stroke="#fff" stroke-width="3" stroke-dasharray="90 16"/><path d="M30 10 17 30h9l-3 14 14-21h-9z" fill="#fff"/></svg></div></div>
      <h3>SOLAR POWER</h3>
      <p>Great value money, great service reliability.<br>These are the key foundations</p>
      <a class="btn-line" href="#">READ MORE</a>
    </div>
  </div>
</section>

<section class="about">
  <h2 class="section-title">ABOUTUS</h2>
  <div class="about-text">
    <p>Varno Electrical was formed to be an expert Electricity Contracting Company providing services to all Residential and Commercial Customers. With over 10 years of experience, Varno Electrical has developed a highly-experienced team of professionals that ensure all our customer expectations are met.</p>
    <p>Varno Electrical was formed to be an expert Electricity Contracting Company providing services to all Residential and Commercial Customers.</p>
  </div>
  <a class="btn-line" href="#">READ MORE</a>
</section>
<div class="photo photo-building" role="img" aria-label="Photo of a commercial building with a red shopfront"></div>

<div class="photo photo-tools" role="img" aria-label="Electrical tools, wiring and a socket on a floor plan"></div>
<section class="why">
  <h2 class="section-title">WHY CHOOSE US?</h2>
  <ul class="why-list">
    <li class="why-item first"><span class="diamond"><span>1</span></span><div class="why-body"><h4>Professional service</h4><p>When you hire a Varno Electrical Electrician you will get a professional and well-presented Electrician</p></div></li>
    <li class="why-item"><span class="diamond"><span>2</span></span><div class="why-body"><h4>5 year workmanship guarantee</h4></div></li>
    <li class="why-item"><span class="diamond"><span>3</span></span><div class="why-body"><h4>Value for Money</h4></div></li>
    <li class="why-item"><span class="diamond"><span>4</span></span><div class="why-body"><h4>Environmentally friendly</h4></div></li>
    <li class="why-item"><span class="diamond"><span>5</span></span><div class="why-body"><h4>Fully insured</h4></div></li>
  </ul>
</section>

<section class="reviews">
  <h2 class="section-title">CLIENT REVIEWS</h2>
  <div class="review" style="left:97px">
    <div class="review-photo" role="img" aria-label="Client business premises photo"></div>
    <p class="review-text">I found Daniel to be well organised, punctual, professional and a good communicator. He did the job at a very reasonable price. A pleasure to deal with."</p>
    <p class="review-name">Marco T. <em>Mount Waverley VIC</em></p>
  </div>
  <div class="review" style="left:637px">
    <div class="review-photo" role="img" aria-label="Client store interior photo"></div>
    <p class="review-text">The service, communication and after sales service of Varno Electrical has been awesome. We would strongly recommend them to any business</p>
    <p class="review-name">Marco T. <em>Mount Waverley VIC</em></p>
  </div>
</section>
<div class="divider"></div>
<div class="clients">
  <div class="client">Lumenhaus</div>
  <div class="client">Outback Supply</div>
  <div class="client">Crestline Plumbing</div>
  <div class="client">Burgerline</div>
</div>

<footer class="footer">
  <div class="col" style="left:97px"><h5>COMPANY</h5><ul><li>Home</li><li>About</li><li>Services</li><li>Testimonial</li><li>Contact us</li></ul></div>
  <div class="col hours" style="left:260px"><h5>HOURS</h5><ul><li>Monday - Friday: 7am - 5pm</li><li>Saturday: 7AM-12PM</li><li>Sunday: Closed</li></ul></div>
  <div class="col" style="left:470px"><h5>OUR POLICY</h5><ul><li>Help &amp; Contact</li><li>Register entry</li><li>Affiliates</li></ul></div>
  <div class="col" style="left:651px"><h5>SUPPORT</h5><ul><li>Get In Touch</li><li>Support Forums</li><li>Knowledge Base</li><li>Request a Quote</li><li>Live Chat Support</li></ul></div>
  <div class="col" style="left:849px"><h5>SUBSCRIBE</h5><div class="field">Name</div><div class="field">Email</div><div class="submit">SUBMIT NOW</div></div>
</footer>
<div class="bottom-bar">Copyrights@2017Company Name, all rights reserved</div>
</body>
</html>
```